AGP letterhead

We need a letterhead design for our new company based in Los Angeles called "Amber Gate Pictures". We develop film and television projects. We work with investors, financiers, film production companies, film distribution and sales companies as well as studios. We would like to incorporate our logo (see attached) but make the letterhead simple and elegant. We need to include: logo, company address, phone number and company website.
Updates

Hello designers, Thanks for your submissions. For our letterhead, we are looking for something more simple and elegant. No heavy bars or lines. Make it feel light and clean. Not a lot of ink on the page. Use the logo and contact info but think "clean", "streamlined" and mostly white paper. Looking forward to seeing more... thanks! Amber Gate Pictures team

Target Market(s)

Studio executives, talent agents and agencies, financiers, investors.

Industry/Entity Type

It Company

Requirements
Must have
• Amber Gate Pictures logo (see attached). Logo may be cropped and altered appropriately for elegant letterhead design.
• Please include:
• COMPANY ADDRESS:
• Tolvane Arts Park
• 2850 Delmore Street
• Crest Hall, 2nd Floor
• Seabrook Bay, CA 90412
• COMPANY WEBSITE:
• www.ambergatepicturesco.example
• COMPANY PHONE NUMBER:
• 555-604-2187

```html
<!DOCTYPE html>
<html lang="en">
<head>
<meta charset="utf-8">
<title>Amber Gate Pictures – Stationery</title>
<link href="https://fonts.googleapis.com/css2?family=Source+Sans+3:wght@400;600;700&display=swap" rel="stylesheet">
<style>
  :root {
    --bg-top: #46565b;
    --bg-bottom: #323f43;
    --paper: #ffffff;
    --ink: #2a2a2a;
    --black: #050505;
    --panel: #0d0f10;
    --brand: #1fa6d8;
    --accent-red: #e0463a;
    --soft-grey: #e4e8ea;
    --flap: #eceff0;
  }
  * { box-sizing: border-box; margin: 0; padding: 0; }
  html, body { width: 1200px; height: 1000px; overflow: hidden; }
  body {
    position: relative;
    background: linear-gradient(160deg, var(--bg-top), var(--bg-bottom));
    font-family: "Source Sans 3", Arial, sans-serif;
    color: var(--ink);
  }
  .sheet {
    position: absolute;
    background: var(--paper);
    border-radius: 12px;
    overflow: hidden;
    box-shadow: 0 8px 14px rgba(0,0,0,.35);
  }
  .brand-name {
    font-family: "Source Sans 3", Arial, sans-serif;
    font-weight: 600;
    color: var(--brand);
    text-align: center;
    text-transform: uppercase;
    letter-spacing: .08em;
    line-height: 1.15;
  }
  .brand-dot {
    display: block;
    margin: 0 auto;
    border-radius: 50%;
    background: var(--brand);
  }

  /* Business cards */
  .card { top: 83px; width: 227px; height: 119px; }
  .card--front { left: 142px; }
  .card--front .black-panel {
    position: absolute; left: 68px; top: 0; width: 92px; height: 100%;
    background: var(--black);
    display: flex; flex-direction: column; align-items: center; justify-content: center; gap: 8px;
  }
  .card--front .brand-dot { width: 26px; height: 26px; }
  .card--front .brand-name { font-size: 9px; }

  .card--back-a { left: 417px; }
  .card--back-b { left: 690px; }
  .card .holder { position: absolute; left: 17px; top: 13px; }
  .card .holder-name { font-size: 13px; font-weight: 400; color: #111; }
  .card .holder-title { font-size: 7px; margin-top: 2px; }
  .card .contact { position: absolute; left: 15px; top: 76px; font-size: 7.5px; line-height: 10.5px; }
  .card--back-a .contact { font-weight: 600; }
  .card .contact dt { display: inline-block; width: 13px; color: var(--brand); }
  .card--back-b .contact dt { color: var(--accent-red); }
  .card .contact dd { display: inline; }
  .card--back-a .black-panel {
    position: absolute; left: 124px; top: 0; width: 60px; height: 100%;
    background: var(--black);
    display: flex; flex-direction: column; align-items: center; justify-content: center; gap: 6px;
  }
  .card--back-a .brand-dot { width: 18px; height: 18px; }
  .card--back-a .brand-name { font-size: 6px; }
  .card--back-b .corner-mark {
    position: absolute; right: -6px; bottom: -8px; width: 90px; height: 90px;
    border-radius: 50%; background: radial-gradient(circle at 45% 45%, #1c2a30, #050708 70%);
  }

  /* Letterhead */
  .letterhead { left: 121px; top: 263px; width: 445px; height: 604px; border-radius: 14px; }
  .letterhead .logo-block {
    position: absolute; left: 182px; top: 0; width: 54px; height: 89px;
    background: var(--black);
    display: flex; flex-direction: column; align-items: center; justify-content: center; gap: 6px;
  }
  .letterhead .brand-dot { width: 20px; height: 20px; }
  .letterhead .brand-name { font-size: 6.5px; }
  .letter { position: absolute; left: 49px; top: 175px; width: 330px; }
  .letter .salutation { font-size: 10.5px; margin-bottom: 24px; }
  .letter .body { font-size: 7px; font-weight: 600; line-height: 12px; text-align: justify; margin-bottom: 14px; }
  .letter .sign-name { font-size: 10.5px; margin-top: 22px; }
  .letter .sign-title { font-size: 6.5px; margin-top: 2px; }
  .letterhead .decor {
    position: absolute; left: 0; bottom: 0; width: 100%; height: 135px;
    background: radial-gradient(ellipse at 85% 85%, var(--soft-grey), rgba(255,255,255,0) 60%),
                radial-gradient(ellipse at 55% 30%, #eef1f2, rgba(255,255,255,0) 45%);
  }
  .letterhead .address {
    position: absolute; left: 40px; top: 543px;
    display: grid; grid-template-columns: 28px 1fr; column-gap: 9px;
    font-size: 5.5px; line-height: 7.5px;
  }
  .letterhead .address dt { color: var(--brand); font-weight: 600; text-align: right; }

  /* Folder */
  .folder { left: 635px; top: 263px; width: 445px; height: 604px; border-radius: 14px; }
  .folder .band { position: absolute; left: 192px; top: 0; width: 173px; height: 100%; background: var(--black); }
  .folder .logo-panel {
    position: absolute; left: 203px; top: 163px; width: 146px; height: 197px;
    background: var(--panel);
    display: flex; flex-direction: column; align-items: center; justify-content: center; gap: 18px;
  }
  .folder .brand-dot { width: 58px; height: 58px; }
  .folder .brand-name { font-size: 13px; }
  .folder .flap { position: absolute; right: 0; top: 128px; }
</style>
</head>
<body>

  <section class="sheet card card--front" aria-label="Business card front">
    <div class="black-panel">
      <span class="brand-dot"></span>
      <p class="brand-name">Amber Gate<br>Pictures</p>
    </div>
  </section>

  <section class="sheet card card--back-a" aria-label="Business card back">
    <div class="holder">
      <p class="holder-name">Dana Whitlow</p>
      <p class="holder-title">Co-Founder &amp; CEO</p>
    </div>
    <dl class="contact">
      <div><dt>T:</dt><dd>(555) 318-4420</dd></div>
      <div><dt>M:</dt><dd>dana@yourstudio.example</dd></div>
      <div><dt>W:</dt><dd>yourstudio.example</dd></div>
    </dl>
    <div class="black-panel">
      <span class="brand-dot"></span>
      <p class="brand-name">Amber Gate<br>Pictures</p>
    </div>
  </section>

  <section class="sheet card card--back-b" aria-label="Business card alternate back">
    <div class="holder">
      <p class="holder-name">Dana Whitlow</p>
      <p class="holder-title">Co-Founder &amp; CEO</p>
    </div>
    <dl class="contact">
      <div><dt>T:</dt><dd>(555) 318-4420</dd></div>
      <div><dt>M:</dt><dd>dana@yourstudio.example</dd></div>
      <div><dt>W:</dt><dd>yourstudio.example</dd></div>
    </dl>
    <span class="corner-mark"></span>
  </section>

  <section class="sheet letterhead" aria-label="Letterhead">
    <div class="logo-block">
      <span class="brand-dot"></span>
      <p class="brand-name">Amber Gate<br>Pictures</p>
    </div>

    <article class="letter">
      <p class="salutation">Dear Mr. Harlow,</p>
      <p class="body">Lorem ipsum dolor sit amet, consectetur adipiscing elit. Donec orci purus, luctus vitae dignissim eu, iaculis sed purus. Vivamus faucibus, ipsum nec aliquet viverra, leo mauris condimentum ligula, sit amet sagittis enim ligula quis arcu. Nam egestas tortor id nisi porttitor mattis. In tortor ante, ultricies in suscipit a, tempus non massa. Vivamus et auctor mi. Fusce vel massa nulla. Phasellus nec eros mauris, et scelerisque orci. Donec malesuada orci vitae nulla accumsan porta a id massa. Quisque accumsan iaculis magna sit amet fringilla. Maecenas consequat, magna eget tincidunt semper, odio nibh rutrum mi, id feugiat ante nisi eu risus. Vestibulum nunc orci, rhoncus a placerat in, ultricies in mi. Cras mattis varius eros, vel fringilla nisi suscipit eget.</p>
      <p class="body">Quisque scelerisque sagittis nulla at porttitor. Mauris a justo et tellus interdum tristique. Sed id augue vitae urna euismod commodo aliquet a quam. Pellentesque arcu velit, cursus et malesuada ut, consequat et diam. Nullam erat sem, rhoncus id ullamcorper vitae, rhoncus et arcu. In ultricies ultricies nulla, ut rutrum nisi iaculis at. Donec eu magna a metus ornare faucibus. Fusce aliquet faucibus ultricies. Morbi semper, est id tincidunt gravida, sem arcu adipiscing lacus, ac bibendum nulla leo eu purus. Quisque nec diam sed risus consectetur a ccumsan quis quis nibh. Vestibulum id purus lorem.</p>
      <p class="sign-name">Dana Whitlow</p>
      <p class="sign-title">Co-Founder &amp; CEO</p>
    </article>

    <div class="decor" role="img" aria-label="Soft scattered light spheres decorating the footer"></div>

    <dl class="address">
      <dt>Address :</dt><dd>Tolvane Arts Park<br>2850 Delmore Street Crest Hall,<br>2nd Floor Seabrook Bay, CA 90412</dd>
      <dt>Tel :</dt><dd>555-604-2187</dd>
      <dt>Website :</dt><dd>www.ambergatepicturesco.example</dd>
    </dl>
  </section>

  <section class="sheet folder" aria-label="Presentation folder">
    <div class="band"></div>
    <div class="logo-panel">
      <span class="brand-dot"></span>
      <p class="brand-name">Amber Gate<br>Pictures</p>
    </div>
    <svg class="flap" width="34" height="164" viewBox="0 0 34 164" aria-hidden="true">
      <path d="M34 0 C22 4 14 10 14 24 L14 140 C14 154 22 160 34 164 Z" fill="var(--flap)"/>
    </svg>
  </section>

</body>
</html>
```